HOT TUB - SPAS service needs an business card

I need an business for my company who his specialise in a maintenance,water treatment and cleaning of Hot Tub - Spas for commercial and residential customers. The company operate mainly in the ski resort of Chamonix, Megève and St Gervais. The final product should communicate pure water, cleanest and professional for luxury property's.
I have upload a logo but any improvement on it is welcome.(color,size, details etc..) or any other idea. Thank you
Company Name: 58 BAINS
My name: Lucien Marchetti
Email: lucimarch@examplemail.net
Tel: +33 (0)6 71 58 29 64
Description to be on the card in french(first langage) and in English:
- Spas service
- Entretien, traitement eau, nettoyage.
- Maintenance, water treatment, cleaning.
Industry/Entity Type
Residential
Colors
Designer to choose colors to be used in the design.
Look and feel
Each slider illustrates characteristics of the customer's brand and the style your logo design should communicate.

```html
<!DOCTYPE html>
<html lang="fr">
<head>
<meta charset="utf-8">
<title>58 BAINS – Cartes de visite</title>
<link rel="stylesheet" href="https://fonts.googleapis.com/css2?family=Source+Sans+3:wght@400;600;700&display=swap">
<style>
  :root {
    --page-bg: #eeede9;
    --front-blue: #21a3f6;
    --front-band: #1781dc;
    --band-line: #8fd0ff;
    --back-blue: #1177d8;
    --mark-tone-front: #3cb0f8;
    --mark-tone-back: #2a87de;
    --ink-white: #ffffff;
  }
  * { margin: 0; padding: 0; box-sizing: border-box; }
  html, body {
    width: 1200px;
    height: 1056px;
    overflow: hidden;
    background: var(--page-bg);
    font-family: "Source Sans 3", "Myriad Pro", sans-serif;
    color: var(--ink-white);
  }
  .canvas { position: relative; width: 1200px; height: 1056px; }

  .card {
    position: absolute;
    width: 812px;
    height: 463px;
    overflow: hidden;
    box-shadow: 0 3px 10px rgba(0,0,0,0.18);
  }

  /* Front card */
  .card--front { left: 333px; top: 25px; background: var(--front-blue); }
  .front-band {
    position: absolute; left: 0; top: 0; width: 100%; height: 120px;
    background: var(--front-band);
  }
  .front-band-line {
    position: absolute; left: 0; top: 119px; width: 100%; height: 5px;
    background: var(--band-line);
  }
  .brand-mark-area {
    position: absolute;
    left: 154px; top: 26px; width: 520px; height: 166px;
    background: linear-gradient(180deg, var(--mark-tone-front), var(--front-blue));
    border-radius: 4px;
  }
  .front-text {
    position: absolute; left: 0; width: 100%; text-align: center;
  }
  .company-name {
    top: 193px; left: -6px;
    font-size: 37px; font-weight: 700; letter-spacing: 0.5px;
  }
  .holder-name {
    top: 306px; left: 4px;
    font-size: 34px; font-weight: 700;
  }
  .contact-line {
    font-size: 26px; font-weight: 400;
    display: flex; justify-content: center; align-items: center; gap: 10px;
  }
  .contact-line--phone { top: 360px; left: 4px; font-weight: 600; }
  .contact-line--email { top: 398px; left: 0; }
  .contact-icon { width: 24px; height: 24px; flex: none; }

  /* Back card */
  .card--back { left: 65px; top: 532px; background: var(--back-blue); }
  .back-name {
    position: absolute; left: 100px; top: 88px; width: 630px; height: 174px;
    display: flex; align-items: center; justify-content: center;
    font-size: 54px; font-weight: 700; letter-spacing: 2px;
    color: var(--ink-white);
  }
  .back-text { position: absolute; left: 0; width: 100%; text-align: center; }
  .service-title {
    top: 318px; left: -6px;
    font-size: 30px; font-weight: 600;
  }
  .service-list {
    font-size: 28px; font-weight: 400; white-space: nowrap;
  }
  .service-list--fr { top: 366px; left: -8px; }
  .service-list--en { top: 404px; left: -10px; }
  .service-list span + span { margin-left: 10px; }
</style>
</head>
<body>
<main class="canvas">

  <section class="card card--front" aria-label="Recto de la carte">
    <div class="front-band"></div>
    <div class="front-band-line"></div>
    <div class="brand-mark-area" role="img" aria-label="Emplacement du logo : dessin au trait d'un chalet, de montagnes et d'un spa"></div>
    <p class="front-text company-name">58 BAINS</p>
    <p class="front-text holder-name">Lucien Marchetti</p>
    <p class="front-text contact-line contact-line--phone">
      <svg class="contact-icon" viewBox="0 0 24 24" aria-hidden="true">
        <path d="M7 3c-1.5 1-3 3-2.6 5.5C5 12 8.5 17 12.5 19.6c2.3 1.4 4.6 1.2 6-.3l1-1.1-3.3-3-1.9 1.3c-2-1-4.2-3.6-5-5.6l1.6-1.6L8.8 3.2z" fill="none" stroke="#fff" stroke-width="1.8" stroke-linejoin="round"/>
      </svg>
      <span>+33 (0)6 71 58 29 64</span>
    </p>
    <p class="front-text contact-line contact-line--email">
      <svg class="contact-icon" viewBox="0 0 24 24" aria-hidden="true">
        <path d="M2 9l10-6 10 6v11H2z" fill="#fff"/>
        <path d="M2 9l10 6 10-6" fill="none" stroke="#21a3f6" stroke-width="1.6"/>
      </svg>
      <span>lucimarch@examplemail.net</span>
    </p>
  </section>

  <section class="card card--back" aria-label="Verso de la carte">
    <p class="back-name">58 BAINS</p>
    <p class="back-text service-title">SPAS SERVICES</p>
    <p class="back-text service-list service-list--fr">
      <span>•Entretien</span><span>•traitement eau</span><span>•nettoyage</span>
    </p>
    <p class="back-text service-list service-list--en">
      <span>•Maintenance</span><span>•water treatment</span><span>•cleaning.</span>
    </p>
  </section>

</main>
</body>
</html>
```